IT company developing solutions for air cargo industry is looking for a new website

We are a professional IT company developing solutions for air cargo industry worldwide.

We are looking to update and completely redesign our current webpages: https://www.brisklane.cz/

What we like about our current pages are the animated graphics on the home page. These could stay, but not a must.

The design of the new pages should be very modern, clean, unique, creative, professional, and to make a statement. We are looking for animated graphics, cool and interesting interactions, cascading layers, etc.

Our company logo is yellow, gray and black. You don’t necessarily have to stick to this colour scheme, however the corporate colors should work well with the overal design of the web pages.
Dark mode pages are also an option.

The scope of the project would include creating a:

• Header
• Footer
• Landing page
• Navigation bar (8 tabs)
• Subpages (10)

In the first stage we are looking only for the header / footer / landing page with navigaton bar / Solutions page design.
As a second round, finalists might be asked to submit another section of the website to see their consistency in terms of the look and feel proposed for the Homepage and Solutions’ pages.
The winning designer will then complete the rest of the pages.

Attached you will find a brief for the first scope of the project. Please read the note section on slide nr. 3 carefully to understand, what we exactly are looking for to achieve.

Industry/Entity Type

Aviation

Number of Pages Required

1 page

Requirements
Must have
• See brief
Nice to have
• See brief
Should not have
• See brief

```html
<!DOCTYPE html>
<html lang="en">
<head>
<meta charset="utf-8">
<title>Aerovane – Air Cargo IT Solutions</title>
<link href="https://fonts.googleapis.com/css2?family=Montserrat:wght@500;600;700&family=Raleway:wght@400;500;600&display=swap" rel="stylesheet">
<style>
:root{
  --gold:#e9b312;
  --ink:#1f1f1f;
  --dark:#232323;
  --grey:#6a6a6a;
  --text-grey:#666;
  --white:#fff;
}
*{margin:0;padding:0;box-sizing:border-box}
html,body{width:671px;height:1200px;overflow:hidden;background:var(--white)}
body{position:relative;font-family:'Raleway',sans-serif;color:var(--ink)}
.abs{position:absolute}

/* header */
.site-header{left:0;top:0;width:671px;height:46px;background:var(--white)}
.brand{left:62px;top:12px;font-family:'Montserrat',sans-serif;font-size:18px;font-weight:600;color:var(--grey)}
.tagline-top{right:69px;top:18px;font-size:9.2px;font-weight:500;color:var(--ink)}

.main-nav{left:0;top:46px;width:671px;height:26px;background:var(--gold);display:flex;justify-content:center;align-items:center;gap:27px}
.main-nav a{font-size:7.4px;color:var(--ink);text-decoration:none;font-weight:500;letter-spacing:.1px}

/* hero */
.hero{left:0;top:72px;width:671px;height:340px;overflow:hidden}
.hero-photo{position:absolute;inset:0;background:linear-gradient(100deg,#2e3137 0%,#3a3630 45%,#2b2a28 100%)}
.hero-shade{position:absolute;inset:0;background:linear-gradient(90deg,rgba(20,20,20,.55),rgba(20,20,20,.2))}
.hero h1{position:absolute;left:62px;top:77px;width:300px;font-family:'Montserrat',sans-serif;font-weight:700;font-size:15.2px;line-height:21px;color:var(--white)}
.hero p{position:absolute;left:61px;top:125px;width:236px;font-size:9.2px;font-weight:500;line-height:15.4px;color:var(--white)}
.btn{position:absolute;left:62px;top:212px;width:97px;height:27px;background:var(--gold);border-radius:4px;font-family:'Montserrat',sans-serif;font-weight:700;font-size:8.4px;color:var(--ink);display:flex;align-items:center;justify-content:center}
.route-circle{position:absolute;left:374px;top:33px;width:264px;height:264px;border-radius:50%;background:var(--white);border:4px solid var(--gold);overflow:hidden}
.route-map{position:absolute;left:4px;top:12px;width:240px;height:205px;border-radius:45% 55% 50% 35%;background:radial-gradient(ellipse at 55% 40%,#b5b5b5 0%,#d6d6d6 50%,rgba(255,255,255,0) 72%)}
.route-label{position:absolute;left:0;width:100%;top:218px;text-align:center;font-family:'Montserrat',sans-serif;font-weight:600;font-size:15px;color:var(--ink)}

/* statement */
.statement{left:100px;top:451px;width:471px;text-align:center;font-family:'Montserrat',sans-serif;font-weight:700;font-size:14.8px;line-height:22px}

.stats{left:59px;top:512px;width:549px;height:118px;background:var(--gold);border-radius:5px;box-shadow:0 3px 8px rgba(0,0,0,.15);display:flex;padding:25px 0 13px}
.stat{flex:1;border-right:1px solid rgba(255,255,255,.8);text-align:center;font-family:'Montserrat',sans-serif}
.stat:last-child{border-right:none}
.stat strong{display:block;font-weight:700;font-size:12.5px;margin-top:8px;margin-bottom:6px}
.stat span{display:block;font-weight:500;font-size:8.8px;line-height:16px}

/* about */
.cargo-photo{left:84px;top:673px;width:241px;height:241px;border-radius:50%;border:3px solid var(--gold);background:linear-gradient(160deg,#e8c8b8 0%,#c9b5a8 35%,#8f8a88 60%,#5a4a3a 85%,#3a3028 100%)}
.about-text{left:346px;top:710px;width:245px;font-size:8.9px;line-height:16.3px;color:var(--text-grey)}

/* footer */
.site-footer{left:0;top:958px;width:671px;height:242px}
.footer-col h3{font-family:'Montserrat',sans-serif;font-weight:600;font-size:11.5px;color:var(--white);margin-bottom:14px}
.footer-col li{list-style:none;font-size:8.2px;color:var(--white);line-height:16.8px;font-weight:500}
.contact li{display:flex;gap:5px;align-items:flex-start}
.contact svg{flex:none;margin-top:3px}
.subscribe{left:494px;top:1022px;width:111px;height:133px;background:var(--gold);border-radius:3px;text-align:center;padding-top:20px}
.subscribe h3{font-family:'Montserrat',sans-serif;font-weight:700;font-size:12px;color:var(--ink)}
.subscribe p{font-size:7.3px;line-height:15.8px;color:#3a3a3a;margin-top:4px}
.email-field{margin:7px auto 0;width:92px;height:21px;border:1px solid var(--ink);border-radius:11px;display:flex;align-items:center;justify-content:space-between;padding:0 2px 0 5px;font-size:5.6px;color:var(--ink)}
.email-field i{width:16px;height:16px;border-radius:50%;background:var(--white);display:flex;align-items:center;justify-content:center}
.footer-rule{left:61px;top:1168px;width:547px;height:1px;background:#d8d8d8}
.copyright{left:0;width:671px;top:1178px;text-align:center;font-size:8.2px;color:var(--white);font-weight:500}
</style>
</head>
<body>

<header class="site-header abs">
  <div class="brand abs">Aerovane</div>
  <div class="tagline-top abs">Affordable IT Solutions That Revolutionize Tomorrow's Air Cargo Today</div>
</header>

<nav class="main-nav abs">
  <a href="#">INDUSTRIES</a><a href="#">SOLUTIONS</a><a href="#">SUPPORT</a><a href="#">CASE STUDIES</a><a href="#">TESTIMONIALS</a><a href="#">NEWS</a><a href="#">ABOUT US</a>
</nav>

<section class="hero abs">
  <div class="hero-photo" role="img" aria-label="Cargo plane over a container yard with trucks at dusk"></div>
  <div class="hero-shade"></div>
  <h1>Seamlessly Connecting The Air Cargo Industry From Manila To Tahiti</h1>
  <p>Blending decades of air cargo knowledge with end-to-end it solutions.Whether you are an airline, gsa, gha, forwarder or e-commerce operator, Our expertise can elevate your daily workflows, cutting down on expenses, time, and errors</p>
  <div class="btn">LEARN MORE</div>
  <div class="route-circle">
    <div class="route-map" role="img" aria-label="Dotted world map with a flight route from Manila to Tahiti"></div>
    <div class="route-label">Manila To Tahiti</div>
  </div>
  <svg class="abs" style="left:0;top:300px" width="671" height="40" viewBox="0 0 671 40">
    <path d="M0 12 Q330 20 560 30 Q640 30 671 12 L671 40 L0 40Z" fill="#fff"/>
    <path d="M0 12 Q330 20 560 30 Q640 30 671 12" fill="none" stroke="#e9b312" stroke-width="4"/>
  </svg>
</section>

<h2 class="statement abs">We are not IT tech experts attempting to do cargo! We are cargo experts with programming skills!</h2>

<section class="stats abs">
  <div class="stat"><strong>2014</strong><span>Established</span></div>
  <div class="stat"><strong>22</strong><span>Employees</span></div>
  <div class="stat"><strong>11,500,000 +</strong><span>Nr. of Annual<br>Electronic<br>Exchanges</span></div>
  <div class="stat"><strong>18</strong><span>Countries<br>covered</span></div>
  <div class="stat"><strong>20+</strong><span>Connected<br>Clients</span></div>
  <div class="stat"><strong>350,000 +</strong><span>Nr. of<br>Annual<br>AWBs</span></div>
</section>

<div class="cargo-photo abs" role="img" aria-label="Cargo pallets being loaded onto an aircraft at sunset"></div>
<p class="about-text abs">All Aerolink solutions were crafted to enhance operational efficiency, ease, and automation in every aspect of air cargo value chain to drive digital transformation. These suite of solutions were developed with the expertise of airlines, general sales agents, handling agents, and forwarders.<br>The Aerolink Family facilitates a distinctive link and interaction among the various components of the systems, while also enabling communication with the internal or external systems of different clients.<br>Additionally, Aerolink solutions are designed in a contemporary setting, allowing for potential future</p>

<footer class="site-footer abs">
  <svg class="abs" style="left:0;top:0" width="671" height="242" viewBox="0 0 671 242">
    <path d="M0 30 Q60 8 160 8 Q420 14 671 27 L671 242 L0 242Z" fill="#232323"/>
    <path d="M0 30 Q60 8 160 8 Q420 14 671 27" fill="none" stroke="#e9b312" stroke-width="4"/>
  </svg>
</footer>

<div class="footer-col abs" style="left:65px;top:1028px">
  <h3>Main Links</h3>
  <ul><li>Case Studies</li><li>Testimonials</li><li>News</li><li>About Us</li></ul>
</div>
<div class="footer-col abs" style="left:200px;top:1028px">
  <h3>Other Links</h3>
  <ul><li>Industries</li><li>Solutions</li><li>Support</li></ul>
</div>
<div class="footer-col contact abs" style="left:334px;top:1028px">
  <h3>Contact Details</h3>
  <ul>
    <li><svg width="8" height="9" viewBox="0 0 8 9"><path d="M2 0 L3.5 2.5 L2.6 3.4 Q3.5 5.5 5 6.4 L6 5.5 L8 7 L7 9 Q2 8 0 1.5Z" fill="#fff"/></svg>+1 555 010 0199</li>
    <li><svg width="9" height="7" viewBox="0 0 9 7"><rect x=".5" y=".5" width="8" height="6" fill="none" stroke="#fff"/><path d="M.5 .5 L4.5 4 L8.5 .5" fill="none" stroke="#fff"/></svg>admin@aerovane<br>.com</li>
    <li><svg width="7" height="9" viewBox="0 0 7 9"><path d="M3.5 9 Q0 5 0 3.5 A3.5 3.5 0 0 1 7 3.5 Q7 5 3.5 9Z" fill="#fff"/><circle cx="3.5" cy="3.5" r="1.3" fill="#232323"/></svg>Lorem Ipsum, Lorem,<br>Lorem, ipsum</li>
  </ul>
</div>

<div class="subscribe abs">
  <h3>Subscribe</h3>
  <p>Subscribe to our<br>newsletter to get all our<br>news in your inbox.</p>
  <div class="email-field">Your Email Address<i><svg width="10" height="7" viewBox="0 0 10 7"><path d="M0 3.5 H9 M6 .5 L9 3.5 L6 6.5" fill="none" stroke="#1f1f1f" stroke-width="1"/></svg></i></div>
</div>

<div class="footer-rule abs"></div>
<div class="copyright abs">© 2024 Aerovane &nbsp;I All Rights Reserved</div>

</body>
</html>
```